One piece Trade show banner, 8' x 8' square

One piece banner for trade show
8' x 8' airborne geophysical company

Target Market(s)

Business

Industry/Entity Type

mineral exploration and science

Colors
0054AA
0677BA
7BADD7
CADEEF
E8F1F8
FFC000
F8CF3A
FAE287
FDF2CF
FEFAEE

Requirements
Must have
• Company logo (attached), slogan (Airborne Geophysics for Discovery). We are looking for a new banner, for a standard 8 x 8' square one-piece booth. I have attached some pictures, our logo, our old banner for reference, and two examples from unrelated companies from a tradeshow that we like. If its possible I'd like to change the color of the helicopter from green to dark grey. IE, keep the orange and white, just change green to dark grey. Looking for a simple, clean design with minimal text.
Nice to have
• I have attached examples of banners that we like (2xIMG), plus our old 3-piece banner r.
Should not have
• Green in the helicopter. Please change the color of the helicopter with green/orange/white to dark grey/orange/white. IE change the green to dark grey and leave the orange and white alone. I've attached lots of pictures but I don't expect them all to be used.

```html
<!DOCTYPE html>
<html lang="en">
<head>
<meta charset="utf-8">
<title>Meridian AeroSurveys – Trade Show Banner</title>
<link rel="stylesheet" href="https://fonts.googleapis.com/css2?family=Poppins:wght@400;500;700;800&display=swap">
<style>
  :root {
    --page-bg: #77706f;
    --banner-white: #ffffff;
    --deep-blue: #0054aa;
    --mid-blue: #0677ba;
    --navy: #1b3782;
    --sky-light: #7badd7;
    --pale-blue: #cadeef;
    --gold: #ffc000;
    --text-white: #ffffff;
    --rock-brown: #6b5446;
    --heli-grey: #4a5560;
    --heli-orange: #f08a1c;
  }
  * { box-sizing: border-box; margin: 0; padding: 0; }
  html, body {
    width: 1200px; height: 2233px; overflow: hidden;
    background: var(--page-bg);
    font-family: "Poppins", sans-serif;
  }
  .banner {
    position: absolute; left: 50px; top: 566px;
    width: 1100px; height: 1100px;
    background: var(--banner-white);
  }

  /* Hero */
  .hero {
    position: absolute; left: 0; top: 0; width: 1100px; height: 625px;
    overflow: hidden;
  }
  .hero-landscape {
    position: absolute; inset: 0;
    background: linear-gradient(180deg, #1a3f8a 0%, #134e95 36%, #1e4d84 50%, #37506a 64%, #55504e 78%, var(--rock-brown) 90%, #8a6a4e 100%);
  }
  .hero-helicopter {
    position: absolute; left: 10px; top: 20px; width: 760px; height: 420px;
    border-radius: 50%;
    background:
      radial-gradient(ellipse 38% 30% at 48% 45%, rgba(240,242,245,0.85) 0%, rgba(200,205,212,0.6) 45%, rgba(74,85,96,0) 100%),
      radial-gradient(ellipse 60% 40% at 40% 50%, rgba(74,85,96,0.55) 0%, rgba(74,85,96,0) 100%),
      radial-gradient(ellipse 12% 18% at 33% 42%, rgba(240,138,28,0.55) 0%, rgba(240,138,28,0) 100%);
  }
  .brand {
    position: absolute; right: 50px; top: 50px;
    display: flex; align-items: center; gap: 12px;
    color: var(--text-white);
    font-weight: 500; font-size: 44px; line-height: 1;
  }
  .brand-dot {
    width: 16px; height: 16px; border-radius: 50%;
    background: var(--text-white);
  }
  .headline {
    position: absolute; left: 0; top: 0; width: 1100px; height: 625px;
  }
  .headline text { fill: var(--text-white); font-family: "Poppins", sans-serif; font-weight: 800; }

  /* Services panel */
  .services {
    position: absolute; left: 60px; top: 625px;
    width: 982px; height: 412px;
    background: linear-gradient(180deg, #1c74b9 0%, #1a5fa6 50%, var(--navy) 100%);
    color: var(--text-white);
    overflow: hidden;
  }
  .services-photo {
    position: absolute; left: 0; top: 0; width: 370px; height: 412px;
    background:
      radial-gradient(ellipse 22% 10% at 62% 10%, rgba(202,222,239,0.75) 0%, rgba(202,222,239,0) 100%),
      radial-gradient(ellipse 32% 20% at 30% 72%, rgba(202,222,239,0.35) 0%, rgba(200,80,90,0.18) 55%, rgba(27,55,130,0) 100%),
      linear-gradient(180deg, rgba(123,173,215,0.25) 0%, rgba(6,119,186,0.1) 55%, rgba(27,55,130,0.2) 100%);
  }
  .service { position: absolute; }
  .service h2 {
    color: var(--gold); font-weight: 700; font-size: 23px; line-height: 27px;
  }
  .service ul { list-style: none; }
  .service li {
    font-size: 22px; line-height: 25px; font-weight: 400;
    padding-left: 16px; text-indent: -16px;
  }
  .service li::before { content: "•"; margin-right: 7px; }
  .em { left: 394px; top: 52px; width: 280px; }
  .radio { left: 394px; top: 179px; width: 280px; }
  .mag { left: 688px; top: 52px; width: 280px; }
  .consult { left: 688px; top: 179px; width: 280px; }
  .website {
    position: absolute; left: 394px; top: 348px;
    font-weight: 700; font-size: 29px; line-height: 34px; letter-spacing: 0.4px;
    white-space: nowrap;
  }
</style>
</head>
<body>
  <main class="banner">
    <section class="hero">
      <div class="hero-landscape" role="img" aria-label="Photo of a misty rocky plateau under a deep blue sky"></div>
      <div class="hero-helicopter" role="img" aria-label="Photo of a dark grey, orange and white survey helicopter carrying a long sensor boom"></div>
      <div class="brand"><span class="brand-dot"></span><span class="brand-name">Meridian AeroSurveys</span></div>
      <svg class="headline" viewBox="0 0 1100 625" xmlns="http://www.w3.org/2000/svg">
        <text x="56" y="514" font-size="196" textLength="990" lengthAdjust="spacingAndGlyphs">AIRBORNE</text>
        <text x="58" y="605" font-size="70" textLength="986" lengthAdjust="spacingAndGlyphs">GEOPHYSICS FOR DISCOVERY</text>
      </svg>
    </section>

    <section class="services">
      <div class="services-photo" role="img" aria-label="Photo of a helicopter towing an electromagnetic survey loop over the sea"></div>

      <div class="service em">
        <h2>ELECTROMAGNETICS</h2>
        <ul><li>Time domain</li><li>Passive</li><li>VLF-EM</li></ul>
      </div>
      <div class="service radio">
        <h2>RADIOMETRICS</h2>
        <ul><li>256/512 channels</li><li>Up to 42 litres</li></ul>
      </div>
      <div class="service mag">
        <h2>MAGNETICS</h2>
        <ul><li>Helicopter, fixed wing,<br>and drone</li><li>Total field &amp; gradient</li></ul>
      </div>
      <div class="service consult">
        <h2>CONSULTING</h2>
        <ul><li>Survey design</li><li>Interpretations</li><li>Inversions</li></ul>
      </div>

      <p class="website">WWW.MERIDIANAEROSURVEYS.COM</p>
    </section>
  </main>
</body>
</html>
```